Career Development Skills | Business Card & Logo Design

We are looking for a business card including logo design for a new Sydney based business called 'Bright Pathwork'.
We offer a range of services that focus on building the Employability or Employment skills for individuals focusing on job seekers and those interested in building skills required to develop their career. Employability skills are required not only to gain employment, but also to progress within an organisation so as to achieve one's potential.
Updates
Target Market(s)
Our client targets include corporates and govt agencies looking to build skills within their current employee base or assist staff in the transition between roles or workplaces.
Industry/Entity Type
Business
Look and feel
Each slider illustrates characteristics of the customer's brand and the style your logo design should communicate.

```html
<!DOCTYPE html>
<html lang="en">
<head>
<meta charset="utf-8">
<title>Bright Pathwork – Business Card</title>
<link rel="stylesheet" href="https://fonts.googleapis.com/css2?family=Cinzel:wght@700&family=Saira+Condensed:wght@400&display=swap">
<style>
  :root {
    --page-bg: #1c1c1c;
    --front-bg: #1f1f1f;
    --back-bg-light: #f4f4f4;
    --back-bg-dark: #c9cacb;
    --teal: #1a9c9c;
    --orange: #e9741f;
    --grey-text: #6b6b6b;
    --mark-grey: #9a9a9a;
  }
  html, body {
    margin: 0;
    padding: 0;
    width: 1200px;
    height: 1164px;
    overflow: hidden;
    background: var(--page-bg);
  }
  .canvas {
    position: relative;
    width: 1200px;
    height: 1164px;
  }
  .card {
    position: absolute;
    box-shadow: 0 6px 18px rgba(0,0,0,0.6);
  }
  /* Front of card */
  .card-front {
    left: 89px;
    top: 113px;
    width: 724px;
    height: 441px;
    background: var(--front-bg);
    border: 1px solid #333;
  }
  .brand-mark {
    position: absolute;
    left: 320px;
    top: 128px;
    width: 84px;
    height: 84px;
    border-radius: 50%;
    background: var(--mark-grey);
  }
  .brand-rule {
    position: absolute;
    left: 156px;
    top: 258px;
    width: 424px;
    height: 2px;
    background: var(--orange);
  }
  .brand-name {
    position: absolute;
    left: 0;
    top: 270px;
    width: 724px;
    margin: 0;
    text-align: center;
    font-family: "Cinzel", serif;
    font-weight: 700;
    font-size: 31px;
    letter-spacing: 1px;
    color: var(--teal);
  }
  /* Back of card */
  .card-back {
    left: 390px;
    top: 598px;
    width: 720px;
    height: 440px;
    background: linear-gradient(100deg, var(--back-bg-dark) 0%, #e2e3e3 40%, var(--back-bg-light) 100%);
    font-family: "Saira Condensed", sans-serif;
    font-size: 17px;
    line-height: 20px;
  }
  .contact-divider {
    position: absolute;
    left: 157px;
    top: 100px;
    width: 1px;
    height: 248px;
    background: var(--orange);
  }
  .contact-block {
    position: absolute;
    left: 188px;
    margin: 0;
  }
  .contact-person { top: 96px; color: var(--orange); }
  .contact-address { top: 186px; color: var(--grey-text); }
  .contact-phones { top: 304px; left: 185px; color: var(--orange); }
  .contact-phones .number { color: var(--grey-text); }
  .contact-block p { margin: 0; }
</style>
</head>
<body>
<main class="canvas">
  <section class="card card-front" aria-label="Card front">
    <div class="brand-mark" aria-hidden="true"></div>
    <div class="brand-rule"></div>
    <h1 class="brand-name">Bright Pathwork</h1>
  </section>

  <section class="card card-back" aria-label="Card back">
    <div class="contact-divider"></div>
    <div class="contact-block contact-person">
      <p>Daniel Hollis - Director</p>
      <p>Brightpathwork.com.au</p>
      <p>Daniel@brightpathwork.com.au</p>
    </div>
    <address class="contact-block contact-address" style="font-style:normal">
      <p>Level 14</p>
      <p>Harbour Gate Tower 3</p>
      <p>88&nbsp;&nbsp;&nbsp; Kent Lane</p>
      <p>Harbour Gate, Sydney 2000</p>
    </address>
    <div class="contact-block contact-phones">
      <p>Tell ---------------- <span class="number">(02)&nbsp; 95550142</span></p>
      <p>&nbsp;Fax --------------- <span class="number">(02)&nbsp; 95550143</span></p>
    </div>
  </section>
</main>
</body>
</html>
```